NZ First of it's kind solutions directory and marketplace for busy Mums needs a business card design

We need a business card design for our new nationwide business in NZ (long term plans to go global). We provide solutions to the everyday challenges that busy Mums face by connecting them with quality communities and suppliers of carefully selected, relevant products and services. We sell direct via our online marketplace. The final design should communicate our values of inclusivity, quality and smart solutions. Colours should incorporate our logo colour palette of #477077 and #6ba8b2. Our website is at https://www.brightnestmums.example

Target Market(s)

busy Mums, Age 28 – 50, female, income over $100K, location main centres NZ primarily but NZ wide. Is likely juggling work or career with a young family. Probably had hobbies which have fallen by the wayside.
-Wants to succeed in her chosen career without compromising on family life
-to successfully juggle her career without feeling like she is compromising her children
- Is time poor, something always has to give and it’s generally her health (she’ll stay up late, get stressed)
- probably ex corporate or professional career. Has discretional income

Industry/Entity Type

Business

Contact Information for Business Card

Lena Forbisher, Founder, BrightNestMums.example (Strapline Tap; Gather; Sorted), 47 Kowhai Terrace, Ellerslie, Auckland 1051, New Zealand. Mob: 021 483 517 Ph: +64 (0)9 571 4860

Font styles to use
Other font styles liked:
• Raleway, and/or Architects Daughter

Colors
00a990
33b8a4
86cfc6
cfeae6

Requirements
Must have
• the above details, streamline. the logo and colours associated with those logos
Should not have
• foil or metallic colours

```html
<!DOCTYPE html>
<html lang="en">
<head>
<meta charset="utf-8">
<title>BrightNestMums – Business Card</title>
<link href="https://fonts.googleapis.com/css2?family=Roboto:wght@400;500;700&family=Roboto+Condensed:wght@700&display=swap" rel="stylesheet">
<style>
  :root {
    --teal-deep: #477077;
    --teal-light: #6ba8b2;
    --card-white: #fbfbfb;
    --ink: #4a4a4a;
    --backdrop: #e8e5e0;
  }
  html, body {
    margin: 0;
    padding: 0;
    width: 1200px;
    height: 886px;
    overflow: hidden;
    background: var(--backdrop);
  }
  .stage {
    position: relative;
    width: 1200px;
    height: 886px;
    display: flex;
    justify-content: center;
    align-items: center;
    gap: 70px;
  }
  .card {
    width: 330px;
    height: 560px;
    border-radius: 2px;
    box-shadow: 0 6px 18px rgba(0,0,0,0.12);
    position: relative;
    overflow: hidden;
  }
  .card--front {
    background: var(--card-white);
    display: flex;
    flex-direction: column;
    align-items: center;
    padding-top: 178px;
    box-sizing: border-box;
    font-family: "Roboto", Arial, sans-serif;
    text-align: center;
  }
  .brand-dot {
    width: 62px;
    height: 62px;
    border-radius: 50%;
    background: var(--teal-deep);
  }
  .person-name {
    margin: 18px 0 0;
    font-family: "Roboto Condensed", "Arial Narrow", sans-serif;
    font-weight: 700;
    font-size: 23px;
    letter-spacing: 0.2px;
    color: var(--teal-deep);
    text-transform: uppercase;
  }
  .person-role {
    margin: 1px 0 0;
    font-size: 13px;
    letter-spacing: 1.4px;
    color: var(--teal-light);
    text-transform: uppercase;
  }
  .rule {
    width: 26px;
    height: 1px;
    background: var(--teal-light);
    margin: 14px 0;
  }
  .address, .contacts {
    margin: 0;
    font-size: 13px;
    line-height: 1.45;
    color: var(--ink);
    font-style: normal;
  }
  .contacts .label {
    font-weight: 700;
    color: var(--teal-deep);
    text-transform: uppercase;
  }
  .card--back {
    background: var(--teal-deep);
  }
  .back-brand {
    position: absolute;
    left: 50%;
    top: 50%;
    transform: translate(-50%, -50%) rotate(90deg);
    display: flex;
    align-items: center;
    gap: 14px;
    white-space: nowrap;
  }
  .back-brand .brand-dot {
    width: 40px;
    height: 40px;
    background: #ffffff;
  }
  .back-brand .brand-name {
    font-family: "Roboto", Arial, sans-serif;
    font-weight: 700;
    font-size: 38px;
    letter-spacing: -0.5px;
    color: #ffffff;
  }
</style>
</head>
<body>
  <main class="stage">
    <section class="card card--front" aria-label="Business card front">
      <div class="brand-dot" aria-hidden="true"></div>
      <h1 class="person-name">Lena Forbisher</h1>
      <p class="person-role">Founder</p>
      <div class="rule"></div>
      <address class="address">47 Kowhai Terrace, Ellerslie<br>Auckland 1051, New Zealand.</address>
      <div class="rule"></div>
      <p class="contacts">
        <span class="label">Phone:</span> +64 (0)9 571 4860<br>
        <span class="label">Mobile:</span> 021 483 517<br>
        <span class="label">Web:</span> BrightNestMums.example
      </p>
    </section>
    <section class="card card--back" aria-label="Business card back">
      <div class="back-brand">
        <div class="brand-dot" aria-hidden="true"></div>
        <span class="brand-name">BrightNestMums</span>
      </div>
    </section>
  </main>
</body>
</html>
```